LEARN Business Skills so you can Earn a good living

size of the poster is 8”x 10.75" plus 0.25" bleed.
Please leave 1 inch on the bottoum for footer
I want a design a poster that will attract people's attention.
I appreciate a creative ad however the ad should not take away from being able to clearly read the text.
-I also appreciate a simple creative ad that is not too busy.
-you can use graphics, vectors, or pictures of real people.
-however, if you use real people it should be a white male that is wearing a white shirt and look like a professional person.

Target Market(s)

Potential young business people

Industry/Entity Type

education

Requirements
Must have
• easy to read the text
Nice to have
• I would like a "creative" simple ad that is easy to be read
Should not have
• pictures of women

```html
<!DOCTYPE html>
<html lang="en">
<head>
<meta charset="utf-8">
<title>Learn It To Earn It – Business Enrichment Course</title>
<link href="https://fonts.googleapis.com/css2?family=Poppins:wght@300;400;600;700;800&display=swap" rel="stylesheet">
<style>
  :root {
    --ink: #1c1c1c;
    --band: #232323;
    --paper: #ffffff;
    --rule: #bdbdbd;
    --line-light: #d9d9d9;
    --icon-fill: #7a7a7a;
    --photo-light: #f4f5f7;
    --photo-mid: #dfe3e8;
    --photo-deep: #c9ced6;
  }
  * { margin: 0; padding: 0; box-sizing: border-box; }
  html, body { width: 800px; height: 1200px; overflow: hidden; background: var(--paper); }
  body { font-family: "Poppins", sans-serif; color: var(--ink); }
  .poster { position: relative; width: 800px; height: 1200px; overflow: hidden; background: var(--paper); }

  .hero-photo {
    position: absolute; left: 0; top: 0; width: 800px; height: 814px;
    background:
      linear-gradient(180deg, var(--paper) 0%, rgba(255,255,255,0.85) 16%, rgba(255,255,255,0) 38%),
      linear-gradient(90deg, rgba(255,255,255,0.75) 0%, rgba(255,255,255,0.35) 45%, rgba(255,255,255,0) 70%),
      linear-gradient(160deg, var(--photo-light) 0%, var(--photo-mid) 60%, var(--photo-deep) 100%);
  }

  .headline { position: absolute; left: 40px; top: 58px; line-height: 1; }
  .headline-top { font-size: 176px; letter-spacing: -4px; display: block; white-space: nowrap; }
  .headline-bottom { font-size: 112px; letter-spacing: -3px; display: block; margin-top: 4px; white-space: nowrap; }
  .strong { font-weight: 800; }
  .light { font-weight: 300; }

  .rule { position: absolute; left: 44px; width: 460px; height: 1px; background: var(--rule); }
  .rule-top { top: 383px; }
  .rule-mid { top: 530px; }

  .course-title {
    position: absolute; left: 43px; top: 410px;
    font-size: 43px; font-weight: 700; line-height: 1.06; letter-spacing: -0.5px;
  }
  .tagline {
    position: absolute; left: 44px; top: 548px;
    font-size: 30px; font-weight: 600; line-height: 1.18; letter-spacing: -0.3px;
  }

  .footer-band { position: absolute; left: 0; top: 814px; width: 800px; height: 386px; background: var(--band); }

  .skills-box {
    position: absolute; left: 54px; top: 884px; width: 691px; height: 176px;
    border: 1.5px solid var(--line-light); border-radius: 14px;
  }
  .skills-label {
    position: absolute; left: 96px; top: 857px; width: 606px; height: 48px;
    background: var(--paper); border-radius: 24px;
    font-size: 29px; font-weight: 700; color: var(--ink);
    display: flex; align-items: center; justify-content: center; letter-spacing: -0.2px;
    box-shadow: 0 0 0 10px var(--band);
  }
  .skills-row { position: absolute; left: 54px; top: 912px; width: 691px; height: 138px; display: flex; }
  .skill { flex: 1; display: flex; flex-direction: column; align-items: center; color: var(--paper); }
  .skill + .skill { border-left: 1px solid #555; }
  .skill-icon { width: 56px; height: 56px; }
  .skill-text { margin-top: 10px; font-size: 20px; font-weight: 600; line-height: 1.2; text-align: center; }

  .topics {
    position: absolute; left: 30px; top: 1086px; width: 740px;
    color: var(--paper); font-size: 12.3px; font-weight: 400; line-height: 1.33; text-align: center;
  }
</style>
</head>
<body>
<main class="poster">
  <div class="hero-photo" role="img" aria-label="Photo of a young professional man in a white shirt and glasses reviewing papers at a desk with a laptop, bright office shelves behind"></div>

  <h1 class="headline">
    <span class="headline-top"><span class="strong">LEARN</span> <span class="light">IT</span></span>
    <span class="headline-bottom"><span class="light">TO</span> <span class="strong">EARN</span> <span class="light">IT</span></span>
  </h1>

  <div class="rule rule-top"></div>
  <h2 class="course-title">BUSINESS<br>ENRICHMENT COURSE</h2>
  <div class="rule rule-mid"></div>
  <p class="tagline">A proven success of<br>helping people in their<br>livelihoods</p>

  <section class="footer-band" aria-label="Course benefits"></section>
  <div class="skills-box"></div>
  <div class="skills-label">BUSINESS SKILLS THAT WILL HELP YOU</div>

  <div class="skills-row">
    <div class="skill">
      <svg class="skill-icon" viewBox="0 0 56 56" aria-hidden="true">
        <circle cx="28" cy="28" r="27" fill="var(--icon-fill)" stroke="#ddd" stroke-width="1.5"/>
        <rect x="18" y="15" width="20" height="16" rx="2" fill="none" stroke="#fff" stroke-width="1.6"/>
        <circle cx="28" cy="33" r="6" fill="none" stroke="#fff" stroke-width="1.6"/>
        <path d="M24 38 L22 44 L26 42 L28 45 L30 42 L34 44 L32 38" fill="none" stroke="#fff" stroke-width="1.4"/>
      </svg>
      <div class="skill-text">Get a<br>quality job</div>
    </div>
    <div class="skill">
      <svg class="skill-icon" viewBox="0 0 56 56" aria-hidden="true">
        <circle cx="28" cy="28" r="27" fill="var(--icon-fill)" stroke="#ddd" stroke-width="1.5"/>
        <rect x="15" y="32" width="5" height="9" fill="none" stroke="#fff" stroke-width="1.5"/>
        <rect x="22" y="28" width="5" height="13" fill="none" stroke="#fff" stroke-width="1.5"/>
        <rect x="29" y="24" width="5" height="17" fill="none" stroke="#fff" stroke-width="1.5"/>
        <rect x="36" y="19" width="5" height="22" fill="none" stroke="#fff" stroke-width="1.5"/>
        <path d="M14 27 L24 20 L30 22 L40 14 M35 14 H40 V19" fill="none" stroke="#fff" stroke-width="1.6"/>
      </svg>
      <div class="skill-text">Start/grow<br>your business</div>
    </div>
    <div class="skill">
      <svg class="skill-icon" viewBox="0 0 56 56" aria-hidden="true">
        <circle cx="28" cy="28" r="27" fill="var(--icon-fill)" stroke="#ddd" stroke-width="1.5"/>
        <rect x="15" y="26" width="26" height="14" rx="1.5" fill="none" stroke="#fff" stroke-width="1.6"/>
        <circle cx="28" cy="33" r="3.5" fill="none" stroke="#fff" stroke-width="1.5"/>
        <path d="M15 43 H41" stroke="#fff" stroke-width="1.5"/>
        <path d="M17 22 L25 16 L30 19 L39 12 M34 12 H39 V17" fill="none" stroke="#fff" stroke-width="1.6"/>
      </svg>
      <div class="skill-text">Increase your<br>salary</div>
    </div>
  </div>

  <p class="topics">
    BUSINESS ADMIISTRATION &nbsp;|&nbsp; SMALL BUSINESS MANAGEMENT &nbsp;|&nbsp; FINANCE | INVESTMENTS &nbsp;|&nbsp; COMPUTERS &nbsp;|&nbsp; ACCOUNTING<br>
    SALES &nbsp;|&nbsp; MARKETING &nbsp;|&nbsp; PROJECT MANAGEMENT INTERVIEWING SKILLS &nbsp;|&nbsp; BUSINESS LAW &nbsp;|&nbsp; NEGOTIATION &nbsp;|&nbsp; PUBLIC SPEAKING<br>
    IMPORT/EXPORT &nbsp;|&nbsp; INFORMATION TECHNOLOY &nbsp;|&nbsp; DISTRIBUTION &nbsp;|&nbsp; MARKETING &nbsp;|&nbsp; LEDGERLINE &nbsp;|&nbsp; REAL ESTATE<br>
    HEALTH CARE-MANAGEMENT &nbsp;|&nbsp; SHOPVALE
  </p>
</main>
</body>
</html>
```